Business Card Design for Marketing Firm

Looking for business card design for higher end marketing firm. Clean but impressionable/trendy. We are a marketing firm that represents manufacturers in the foodservice equipment and supply industry. Our customers are end users such has hotels, restaurants, country clubs, convention centers and casinos as well as distributors of restaurants supplies and equipment, and manufacturers of foodservice equipment and supplies.
Target Market(s)
Hotels, Restaurants, Supply & Equipment Distributors, Foodservice Manufacturers
Industry/Entity Type
Foodservice/Hospitality
Contact Information for Business Card
Name, Title, Contact Number, Email, Website, Social Media, Address
Requirements
Must have
- Clean & Simple but Serious and Impressionable

```html
<!DOCTYPE html>
<html lang="en">
<head>
<meta charset="utf-8">
<title>Meridian Trade Partners – Business Card</title>
<link href="https://fonts.googleapis.com/css2?family=Open+Sans:wght@400;700&display=swap" rel="stylesheet">
<style>
  :root {
    --navy: #2b2a78;
    --ink: #3a3a44;
    --paper: #ffffff;
    --backdrop: #d9d9d7;
  }
  * { box-sizing: border-box; margin: 0; padding: 0; }
  html, body { width: 1200px; height: 801px; overflow: hidden; }
  body {
    background: var(--backdrop);
    font-family: "Open Sans", Arial, sans-serif;
    position: relative;
  }
  .card {
    position: absolute;
    top: 250px;
    width: 520px;
    height: 300px;
    background: var(--paper);
    box-shadow: 0 6px 18px rgba(0,0,0,0.18);
    overflow: hidden;
  }
  .card--contact { left: 45px; }
  .card--brand { left: 635px; }

  .brand-name {
    position: absolute;
    display: flex;
    align-items: center;
    font-family: "Open Sans", Arial, sans-serif;
    font-weight: 700;
    color: var(--navy);
    white-space: nowrap;
  }
  .brand-name__dot { flex: none; border-radius: 50%; background: var(--navy); }

  .card--contact .brand-name { left: 26px; top: 96px; font-size: 17px; gap: 8px; }
  .card--contact .brand-name__dot { width: 14px; height: 14px; }

  .card--brand .brand-name {
    left: 0; right: 0; top: 108px;
    justify-content: center;
    font-size: 30px; gap: 12px;
  }
  .card--brand .brand-name__dot { width: 22px; height: 22px; }

  .divider {
    position: absolute;
    left: 282px; top: 40px;
    width: 1.5px; height: 150px;
    background: var(--navy);
  }
  .contact { position: absolute; left: 300px; top: 34px; color: var(--ink); }
  .contact__name { font-weight: 700; font-size: 17px; color: var(--navy); letter-spacing: 0.3px; }
  .contact__title { font-size: 11.5px; margin-bottom: 8px; }
  .contact__row { display: flex; align-items: center; gap: 6px; font-size: 12px; line-height: 18px; }
  .contact__row svg { width: 11px; height: 11px; flex: none; }
  .contact__address { font-size: 12px; line-height: 17px; margin-top: 8px; }

  .swoosh { position: absolute; left: 0; bottom: 0; width: 520px; height: 300px; }

  .social { position: absolute; left: 0; right: 0; top: 200px; display: flex; justify-content: center; gap: 5px; }
  .social__dot { width: 16px; height: 16px; border-radius: 50%; background: var(--navy); }
</style>
</head>
<body>

<section class="card card--contact">
  <p class="brand-name"><span class="brand-name__dot"></span>Meridian Trade Partners</p>

  <div class="divider"></div>

  <div class="contact">
    <p class="contact__name">DANIEL REED</p>
    <p class="contact__title">Managing Director</p>
    <p class="contact__row">
      <svg viewBox="0 0 12 12"><circle cx="6" cy="6" r="6" fill="#2b2a78"/><path d="M4 3.2l1 1.2-.6.8c.4.8 1 1.4 1.8 1.8l.8-.6 1.2 1-.6 1c-2.2-.2-4-2-4.2-4.2z" fill="#fff"/></svg>
      123 456 789
    </p>
    <p class="contact__row">
      <svg viewBox="0 0 12 12"><circle cx="6" cy="6" r="6" fill="#2b2a78"/><rect x="3" y="4" width="6" height="4.2" fill="none" stroke="#fff" stroke-width="0.9"/><path d="M3 4l3 2.3L9 4" fill="none" stroke="#fff" stroke-width="0.9"/></svg>
      info@meridiantrade.com
    </p>
    <p class="contact__row">
      <svg viewBox="0 0 12 12"><circle cx="6" cy="6" r="6" fill="#2b2a78"/><circle cx="6" cy="6" r="3.2" fill="none" stroke="#fff" stroke-width="0.8"/><path d="M2.8 6h6.4M6 2.8c-1.6 2-1.6 4.4 0 6.4M6 2.8c1.6 2 1.6 4.4 0 6.4" fill="none" stroke="#fff" stroke-width="0.7"/></svg>
      www.meridiantrade.com
    </p>
    <p class="contact__address">Your address, City<br>State, Zip 1234</p>
  </div>

  <svg class="swoosh" viewBox="0 0 520 300" aria-hidden="true">
    <path d="M0 300 L0 288 C170 284 360 250 520 128 L520 300 Z" fill="var(--navy)"/>
    <path d="M0 270 C170 268 360 236 520 110" fill="none" stroke="var(--navy)" stroke-width="4"/>
  </svg>
</section>

<section class="card card--brand">
  <p class="brand-name"><span class="brand-name__dot"></span>Meridian Trade Partners</p>
  <div class="social" role="img" aria-label="Social media profiles">
    <span class="social__dot"></span>
    <span class="social__dot"></span>
    <span class="social__dot"></span>
    <span class="social__dot"></span>
    <span class="social__dot"></span>
    <span class="social__dot"></span>
  </div>
</section>

</body>
</html>
```